Business Cards for a law firm

Business cards for our law firm. Use our silhoette logo and OAK PARTNERS - check our website (www.oakpartners.example)

Contact Information for Business Card

our silhouette logo, OAK PARTNERS, 800-555-0147, Dorian Pemberton, dorian@oakpartners.example

Requirements
Must have
• our silhouette logo, OAK PARTNERS, 800-555-0147, Dorian Pemberton, dorian@oakpartners.example

```html
<!DOCTYPE html>
<html lang="en">
<head>
<meta charset="utf-8">
<title>Oak Partners – Business Cards</title>
<link rel="stylesheet" href="https://fonts.googleapis.com/css2?family=Montserrat:wght@500;600&family=Open+Sans:wght@400;700&display=swap">
<style>
  :root {
    --navy: #1f2a78;
    --navy-deep: #17205e;
    --navy-soft: #2b3a99;
    --ink: #2a2a35;
    --paper: #ffffff;
    --mist: #b4b4cc;
    --stage: #2b2d31;
  }
  * { margin: 0; padding: 0; box-sizing: border-box; }
  html, body { width: 1200px; height: 900px; overflow: hidden; }
  body {
    background: var(--stage);
    font-family: "Open Sans", sans-serif;
    position: relative;
  }
  .card {
    position: absolute;
    width: 560px;
    height: 320px;
    left: 320px;
    border-radius: 4px;
    overflow: hidden;
    box-shadow: 0 10px 30px rgba(0,0,0,.45);
  }

  /* Front */
  .card-front { top: 100px; background: var(--paper); }
  .front-band {
    position: absolute; left: 12px; top: 0; bottom: 0; width: 78px;
    background: var(--navy);
  }
  .band-mark {
    position: absolute; left: 22px; top: 24px;
    width: 34px; height: 34px; border-radius: 50%;
    background: var(--paper);
  }
  .firm-heading {
    position: absolute; left: 104px; top: 24px;
    font-family: "Montserrat", sans-serif; font-weight: 600;
    font-size: 40px; letter-spacing: 4px; line-height: 1;
    color: var(--navy); white-space: nowrap;
  }
  .contact {
    position: absolute; left: 112px; top: 96px;
    color: var(--ink); font-size: 11.5px; line-height: 1.5;
    white-space: nowrap;
  }
  .contact .person {
    font-weight: 700; font-size: 20px; color: var(--navy); line-height: 1.25;
  }
  .contact .role { font-size: 11px; margin-bottom: 4px; }
  .contact .line { display: flex; align-items: center; gap: 6px; }
  .contact .line svg { width: 10px; height: 10px; fill: var(--navy); flex: none; }
  .figure-art {
    position: absolute; right: 24px; bottom: 6px; width: 240px; height: 190px;
    background: radial-gradient(closest-side, var(--mist) 0%, rgba(180,180,204,.55) 50%, rgba(255,255,255,0) 100%);
  }

  /* Back */
  .card-back {
    top: 480px;
    background: linear-gradient(160deg, var(--navy-soft), var(--navy) 55%, var(--navy-deep));
  }
  .back-pattern {
    position: absolute; inset: 0;
    background: linear-gradient(180deg, rgba(80,110,210,.25), rgba(20,30,90,.15));
  }
  .back-brand {
    position: absolute; left: 50%; top: 50%;
    transform: translate(-50%, -50%);
    display: flex; align-items: center; gap: 14px;
    white-space: nowrap;
  }
  .back-brand .mark {
    width: 30px; height: 30px; border-radius: 50%; background: var(--paper); flex: none;
  }
  .back-brand .name {
    font-family: "Montserrat", sans-serif; font-weight: 500;
    font-size: 24px; letter-spacing: 4px; color: var(--paper);
  }
</style>
</head>
<body>

<section class="card card-front" aria-label="Business card front">
  <div class="front-band"><div class="band-mark"></div></div>
  <div class="firm-heading">OAK PARTNERS</div>
  <div class="contact">
    <div class="person">Dorian Pemberton</div>
    <div class="role">Lawyer</div>
    <div>57 Linden Avenue, Ste 14</div>
    <div>Harwick, VT 05201</div>
    <div class="line">
      <svg viewBox="0 0 10 10"><path d="M2 0.5 L4 2.5 L3 3.8 Q4.2 6 6.2 7 L7.5 6 L9.5 8 L8 9.5 Q3 9 0.5 2 Z"/></svg>
      <span>800-555-0147</span>
    </div>
    <div class="line">
      <svg viewBox="0 0 10 10"><path d="M0.5 2 H9.5 V8.5 H0.5 Z M0.5 2 L5 5.5 L9.5 2" stroke="#fff" stroke-width="0.6"/></svg>
      <span>dorian@oakpartners.example</span>
    </div>
    <div class="line">
      <svg viewBox="0 0 10 10"><circle cx="5" cy="5" r="4.5"/></svg>
      <span>www.oakpartners.example</span>
    </div>
  </div>
  <div class="figure-art" role="img" aria-label="Large pale illustration of two standing figures"></div>
</section>

<section class="card card-back" aria-label="Business card back">
  <div class="back-pattern" role="img" aria-label="Tiled pattern of standing figure silhouettes in darker blue"></div>
  <div class="back-brand">
    <div class="mark"></div>
    <div class="name">OAK PARTNERS</div>
  </div>
</section>

</body>
</html>
```